Home Remodeler Needs a Website!

Single page (plus contact form) website for small home remodeling company. He's got a few pictures he'd like on the site and needs some basic text. He likes clean, simple designs and is "more traditional" in his stylistic preferences. Most of his business comes from word-of-mouth advertising and so the site is just something he needs for people to feel more comfortable with his business.

Target Market(s)

People who want to remodel their homes

Coding

Coded - Design and coding required

Number of Pages Required

2 page

Requirements
Must have
• Main page to include some or all of the attached images, contact page. Neutral colors. Old domain: lindcroftmeadowbuild.com New domain: qm-ventureworks.com You can pull text from the old site or update it.
Should not have
• No loud colors/loud visual elements

```html
<!DOCTYPE html>
<html lang="en">
<head>
<meta charset="utf-8">
<title>Lindcroft Meadow Homes</title>
<link rel="stylesheet" href="https://fonts.googleapis.com/css2?family=Outfit:wght@400;500;600;700&family=Lato:wght@400;700&display=swap">
<style>
:root{
  --black:#000;
  --ink:#161616;
  --white:#fff;
  --soft:#e9e9e9;
  --field:#ececec;
  --field-text:#777;
  --ring:rgba(255,255,255,.45);
  --orange-a:#f39a3b;
  --orange-b:#e8731c;
}
*{box-sizing:border-box;margin:0;padding:0}
html,body{width:1200px;height:3260px;overflow:hidden;background:var(--black)}
body{position:relative;font-family:"Lato",sans-serif;color:var(--white)}
.abs{position:absolute}
.heading{font-family:"Outfit",sans-serif;font-weight:600;text-transform:uppercase;letter-spacing:.5px;line-height:1.1}
.rule{position:absolute;height:2px;background:var(--white)}

/* header */
.site-header{position:absolute;left:0;top:0;width:1200px;height:101px;background:var(--black)}
.brand{position:absolute;left:66px;top:37px;font-family:"Outfit",sans-serif;font-size:23px;font-weight:500;letter-spacing:.3px}
.main-nav a{position:absolute;top:45px;font-family:"Lato",sans-serif;font-size:12px;color:var(--white);text-decoration:none;letter-spacing:.3px}
.header-phone{position:absolute;left:946px;top:36px;display:flex;align-items:center;gap:10px;font-family:"Outfit",sans-serif;font-size:19px;font-weight:500;letter-spacing:.5px}

/* hero */
.hero{position:absolute;left:0;top:101px;width:1200px;height:666px;overflow:hidden}
.hero-photo{position:absolute;inset:0;background:
  radial-gradient(ellipse at 60% 70%,#8a7358 0%,transparent 55%),
  linear-gradient(180deg,#5e6a6c 0%,#6f7672 40%,#6b5a46 75%,#4a3c2e 100%)}
.hero-ring{position:absolute;left:127px;top:92px;width:430px;height:430px;border-radius:50%;border:5px solid var(--ring);background:rgba(120,120,120,.18)}
.hero-title{position:absolute;left:142px;top:225px;width:400px;text-align:center;font-size:50px;font-weight:700;line-height:49px;text-shadow:0 1px 3px rgba(0,0,0,.25)}
.pill{position:absolute;display:flex;align-items:center;justify-content:center;background:var(--white);color:#111;border-radius:24px;font-family:"Outfit",sans-serif;font-weight:600;text-transform:uppercase}
.hero-cta{left:246px;top:388px;width:181px;height:45px;font-size:15px}
.slider-arrow{position:absolute;top:282px}
.scroll-cue{position:absolute;left:560px;top:566px;width:80px;text-align:center;font-size:13px;letter-spacing:3px}

/* welcome */
.welcome{position:absolute;left:0;top:767px;width:1200px;height:547px;background:var(--black)}
.welcome-title{position:absolute;left:0;top:80px;width:1200px;text-align:center;font-size:40px;line-height:37px}
.welcome-text{position:absolute;left:170px;top:196px;width:860px;text-align:center;font-size:15.5px;line-height:30.2px;color:var(--soft)}

/* services */
.services{position:absolute;left:0;top:1314px;width:1200px;height:632px;background:var(--ink)}
.services-title{position:absolute;left:125px;top:130px;font-size:31px;line-height:36px}
.service-list{position:absolute;list-style:none;font-family:"Outfit",sans-serif;font-size:14px;line-height:25.3px}
.services-note{position:absolute;left:127px;top:362px;width:480px;font-family:"Outfit",sans-serif;font-size:13.5px;line-height:25.3px;color:var(--soft)}
.book-btn{left:127px;top:468px;width:147px;height:45px;font-size:14px;letter-spacing:1px;font-weight:500}
.photo-ring{position:absolute;left:659px;top:69px;width:451px;height:451px;border-radius:50%;border:2px solid #777}
.photo-kitchen{position:absolute;left:675px;top:85px;width:419px;height:419px;border-radius:50%;background:radial-gradient(circle at 45% 30%,#a98a6a 0%,#6b4a31 40%,#2a1e16 80%)}
.photo-bath{position:absolute;left:632px;top:342px;width:242px;height:242px;border-radius:50%;border:3px solid var(--ink);background:radial-gradient(circle at 50% 35%,#c9d3d6 0%,#98a2a2 50%,#6a6258 100%)}

/* about */
.about{position:absolute;left:0;top:1946px;width:1200px;height:497px;background:var(--black)}
.photo-about{position:absolute;left:0;top:0;width:604px;height:497px;background:linear-gradient(135deg,#6f6558 0%,#9a8f86 35%,#4a3226 65%,#2b1d17 100%)}
.about-title{position:absolute;left:671px;top:102px;font-size:31px}
.about-text{position:absolute;left:673px;top:180px;width:420px;font-size:15px;line-height:21px;color:var(--soft)}
.about-text p{margin-bottom:21px}

/* contact */
.contact{position:absolute;left:0;top:2443px;width:1200px;height:602px;overflow:hidden}
.contact-photo{position:absolute;inset:0;background:radial-gradient(ellipse at 50% 30%,#3a3632 0%,#1e1c1a 60%,#101010 100%)}
.contact-title{position:absolute;left:0;top:65px;width:1200px;text-align:center;font-size:35px}
.contact-phones{position:absolute;top:145px;font-family:"Outfit",sans-serif;font-size:21px;font-weight:500;display:flex;align-items:center;gap:10px}
.field{position:absolute;background:var(--field);color:var(--field-text);font-size:13px;padding:0 22px;display:flex;align-items:center}
.field.message{align-items:flex-start;padding-top:22px}
.send-btn{position:absolute;left:499px;top:472px;width:185px;height:51px;border-radius:26px;background:linear-gradient(180deg,var(--orange-a),var(--orange-b));display:flex;align-items:center;justify-content:center;font-family:"Outfit",sans-serif;font-size:18px;font-weight:500;letter-spacing:1.5px}

/* footer */
.site-footer{position:absolute;left:0;top:3045px;width:1200px;height:215px;background:var(--black)}
.footer-nav a{position:absolute;top:52px;transform:translateX(-50%);font-family:"Outfit",sans-serif;font-size:16px;color:var(--white);text-decoration:none}
.copyright{position:absolute;left:0;top:90px;width:1200px;text-align:center;font-size:13px;color:var(--soft)}
.social{position:absolute;top:131px;width:36px;height:36px;border-radius:50%;background:var(--white)}
</style>
</head>
<body>

<header class="site-header">
  <div class="brand">LINDCROFT MEADOW HOMES</div>
  <nav class="main-nav">
    <a style="left:415px">HOME</a>
    <a style="left:519px">SERVICES</a>
    <a style="left:639px">ABOUT US</a>
    <a style="left:766px">CONTACT US</a>
  </nav>
  <div class="header-phone">
    <svg width="32" height="32" viewBox="0 0 32 32"><circle cx="16" cy="16" r="16" fill="#fff"/><path d="M11 8c1-.6 2-.3 2.5.6l1.4 2.6c.4.8.2 1.6-.5 2.1l-1.1.8c.7 2 2.3 3.7 4.3 4.5l.9-1.1c.6-.6 1.4-.8 2.1-.4l2.5 1.5c.8.5 1 1.6.4 2.4-.9 1.3-2.3 2.1-3.9 1.7C13.8 21.6 10 17.5 9.2 12.4 9 10.6 9.7 9 11 8z" fill="#000"/></svg>
    <span>555-014-2286</span>
  </div>
</header>

<section class="hero">
  <div class="hero-photo" role="img" aria-label="Renovated open basement with polished concrete floor, kitchen bar and French doors"></div>
  <div class="hero-ring"></div>
  <h1 class="heading hero-title">Your Dream Luxury Renovation</h1>
  <div class="pill hero-cta">Contact Us</div>
  <svg class="slider-arrow" style="left:20px" width="28" height="52" viewBox="0 0 28 52"><polyline points="24,2 4,26 24,50" fill="none" stroke="#fff" stroke-width="3"/></svg>
  <svg class="slider-arrow" style="left:1146px" width="28" height="52" viewBox="0 0 28 52"><polyline points="4,2 24,26 4,50" fill="none" stroke="#fff" stroke-width="3"/></svg>
  <div class="scroll-cue">SCROLL
    <svg width="24" height="14" viewBox="0 0 24 14" style="display:block;margin:2px auto 0"><polyline points="2,2 12,12 22,2" fill="none" stroke="#fff" stroke-width="1.5"/></svg>
  </div>
</section>

<section class="welcome">
  <h2 class="heading welcome-title">Welcome to Lindcroft<br>Meadow Homes</h2>
  <div class="rule" style="left:578px;top:170px;width:44px"></div>
  <p class="welcome-text">When you want affordable, quality home construction services; think of us to do the job. Since 1981 Warren Ellison has built and remodeled over 400 homes and businesses. Let us be your contractor for the next project you start. When quality, value and personal attention to detail are important With over 20 years experience in residential and commercial construction, you can trust your project to Lindcroft Meadow Homes.<br>"DON'T TINKER AROUND"<br>I have built my business with a partnership of clients, employees, subcontractors, suppliers and inspectors. Since each project is unique, this partnership brings creative ideas to your home. I have deep "hands on" history in construction from foundations to final finishing touches.</p>
</section>

<section class="services">
  <h2 class="heading services-title">Commercial and<br>Residential Contracting</h2>
  <div class="rule" style="left:127px;top:213px;width:45px"></div>
  <ul class="service-list" style="left:128px;top:240px">
    <li>"ALL IN ONE PACKAGE"</li>
    <li>Pre Construction Consultation</li>
    <li>New Construction</li>
    <li>Remodeling / kitchens and baths</li>
  </ul>
  <ul class="service-list" style="left:385px;top:243px">
    <li>Additions</li>
    <li>Porches and Decks</li>
    <li>Specializing in historic renovations.</li>
  </ul>
  <p class="services-note">Providing services for roofing, window replacement, electrical, air conditioning and plumbing upgrades, painting, gutters, concrete work plumbing upgrades, painting, gutters, concrete work</p>
  <div class="pill book-btn">Book Now</div>
  <div class="photo-ring"></div>
  <div class="photo-kitchen" role="img" aria-label="Kitchen with wood cabinets, stone accent wall and island"></div>
  <div class="photo-bath" role="img" aria-label="Bathroom with soaking tub under a window"></div>
</section>

<section class="about">
  <div class="photo-about" role="img" aria-label="Kitchen with stainless steel refrigerator and farmhouse sink"></div>
  <h2 class="heading about-title">About Company</h2>
  <div class="rule" style="left:673px;top:157px;width:44px"></div>
  <div class="about-text">
    <p>I have built my business with a partnership of clients, employees, subcontractors, suppliers and inspectors. Since each project is unique, this partnership brings creative ideas to your home.</p>
    <p>I have deep "hands on" history in construction from foundations to final finishing touches.</p>
    <p>We cultivate suppliers who deliver quality materials on time and without damage</p>
  </div>
</section>

<section class="contact">
  <div class="contact-photo" role="img" aria-label="Dimmed kitchen interior backdrop"></div>
  <h2 class="heading contact-title">Contact Us</h2>
  <div class="rule" style="left:579px;top:112px;width:40px"></div>
  <div class="contact-phones" style="left:400px">
    <svg width="32" height="32" viewBox="0 0 32 32"><circle cx="16" cy="16" r="16" fill="#fff"/><path d="M11 8c1-.6 2-.3 2.5.6l1.4 2.6c.4.8.2 1.6-.5 2.1l-1.1.8c.7 2 2.3 3.7 4.3 4.5l.9-1.1c.6-.6 1.4-.8 2.1-.4l2.5 1.5c.8.5 1 1.6.4 2.4-.9 1.3-2.3 2.1-3.9 1.7C13.8 21.6 10 17.5 9.2 12.4 9 10.6 9.7 9 11 8z" fill="#000"/></svg>
    <span>555-014-2286</span>
  </div>
  <div class="contact-phones" style="left:622px">
    <svg width="32" height="32" viewBox="0 0 32 32"><circle cx="16" cy="16" r="16" fill="#fff"/><path d="M11 8c1-.6 2-.3 2.5.6l1.4 2.6c.4.8.2 1.6-.5 2.1l-1.1.8c.7 2 2.3 3.7 4.3 4.5l.9-1.1c.6-.6 1.4-.8 2.1-.4l2.5 1.5c.8.5 1 1.6.4 2.4-.9 1.3-2.3 2.1-3.9 1.7C13.8 21.6 10 17.5 9.2 12.4 9 10.6 9.7 9 11 8z" fill="#000"/></svg>
    <span>555-014-7390</span>
  </div>
  <div class="field" style="left:196px;top:223px;width:402px;height:47px">First Name*</div>
  <div class="field" style="left:609px;top:223px;width:400px;height:47px">Last Name*</div>
  <div class="field" style="left:196px;top:281px;width:402px;height:48px">Email address*</div>
  <div class="field" style="left:609px;top:281px;width:400px;height:48px">Phone*</div>
  <div class="field message" style="left:197px;top:341px;width:817px;height:109px">Message</div>
  <div class="send-btn">SEND</div>
</section>

<footer class="site-footer">
  <nav class="footer-nav">
    <a style="left:354px">HOME</a>
    <a style="left:506px">SERVICES</a>
    <a style="left:675px">ABOUT US</a>
    <a style="left:844px">CONTACT</a>
  </nav>
  <p class="copyright">© 2021 Lindcroft Meadow Homes &nbsp;|&nbsp; Legal &nbsp;|&nbsp; Term of Use</p>
  <div class="social" style="left:543px" aria-label="Social link"></div>
  <div class="social" style="left:588px" aria-label="Social link"></div>
  <div class="social" style="left:634px" aria-label="Social link"></div>
</footer>

</body>
</html>
```